Unique Business Card Design

Unique Business Card design for our orthotic and prosthetic company. Our logo is on our website, color is light blue. Unique shape (artificial leg shaped, vertical, etc..) preferred. Logo, business name, individual name and basic demographics needed.

Industry/Entity Type

Business

Contact Information for Business Card

Logo, Industry, Phone # Logo, "Prosthetic & Orthotic Services" Place to add individual name and contact info

Colors
cee9f5

Requirements
Must have
• The icon must be there, placement of "Prosthetic & Orthotic Services" can be moved
Nice to have
• Like the mix of light blue, and a little darker blue. One design included the icons from my website which was a nice touch

```html
<!DOCTYPE html>
<html lang="en">
<head>
<meta charset="utf-8">
<title>Limbwell Inc. business cards</title>
<link rel="stylesheet" href="https://fonts.googleapis.com/css2?family=Open+Sans:wght@400;600;700&display=swap">
<style>
  :root {
    --brand-blue: #1560ab;
    --card-white: #ffffff;
    --stage: #e9ecec;
    --ink-grey: #4a4f55;
  }
  * { margin: 0; padding: 0; box-sizing: border-box; }
  html, body { width: 1200px; height: 812px; overflow: hidden; background: var(--stage); }
  body { font-family: "Open Sans", Arial, sans-serif; position: relative; }

  .card {
    position: absolute;
    top: 252px;
    width: 540px;
    height: 309px;
    background: var(--card-white);
    overflow: hidden;
    box-shadow: 0 2px 6px rgba(0,0,0,0.12);
  }
  .card--front { left: 40px; }
  .card--back { left: 620px; }

  /* front */
  .front-lockup {
    position: absolute;
    left: 50%; top: 50%;
    transform: translate(-50%, -50%);
    display: flex; align-items: center; gap: 18px;
  }
  .brand-dot {
    width: 70px; height: 70px; border-radius: 50%;
    background: var(--brand-blue); flex: none;
  }
  .brand-name {
    color: var(--brand-blue);
    font-weight: 600;
    font-size: 30px;
    letter-spacing: 0.5px;
    line-height: 1;
    white-space: nowrap;
  }
  .brand-tagline {
    color: var(--brand-blue);
    font-weight: 600;
    font-size: 14px;
    margin-top: 8px;
    padding-top: 6px;
    border-top: 2px solid var(--brand-blue);
    white-space: nowrap;
  }

  /* back */
  .back-disc {
    position: absolute;
    left: -60px; top: 118px;
    width: 330px; height: 330px;
    border-radius: 50%;
    background: var(--brand-blue);
  }
  .back-info {
    position: absolute;
    right: 26px; top: 22px;
    text-align: right;
    color: var(--ink-grey);
    font-size: 11.5px;
    line-height: 1.35;
  }
  .person-name { color: var(--brand-blue); font-size: 19px; font-weight: 400; line-height: 1.2; }
  .person-name strong { font-weight: 700; }
  .person-name .credentials { font-size: 11px; }
  .back-brand { margin-top: 14px; display: inline-block; text-align: left; }
  .back-brand .brand-name { font-size: 26px; }
  .back-brand .brand-tagline { font-size: 12.5px; }
  .contact-list { list-style: none; margin-top: 12px; }
  .contact-list li { display: flex; justify-content: flex-end; align-items: center; gap: 7px; }
  .contact-list svg { width: 11px; height: 11px; fill: var(--brand-blue); flex: none; }
  .web { margin-top: 2px; }
</style>
</head>
<body>
  <section class="card card--front" aria-label="Card front">
    <div class="front-lockup">
      <span class="brand-dot"></span>
      <div>
        <div class="brand-name">LIMBWELL INC.</div>
        <div class="brand-tagline">Prosthetic &amp; Orthotic Services</div>
      </div>
    </div>
  </section>

  <section class="card card--back" aria-label="Card back">
    <div class="back-disc"></div>
    <div class="back-info">
      <div class="person-name"><strong>Mira</strong> Kessel, <span class="credentials">CO LPO</span></div>
      <div>mkessel@limbwellinc.com</div>
      <div>2290 Harbor Ave.</div>
      <div>Cedar Falls, NY 11400</div>

      <div class="back-brand">
        <div class="brand-name">LIMBWELL INC.</div>
        <div class="brand-tagline">Prosthetic &amp; Orthotic Services</div>
      </div>

      <ul class="contact-list">
        <li>555.210.4400
          <svg viewBox="0 0 12 12" aria-label="phone"><path d="M2.5 1 4.5 1 5.3 3.6 4 4.6C4.7 6 6 7.3 7.4 8L8.4 6.7 11 7.5 11 9.5C11 10.3 10.3 11 9.5 11 5 11 1 7 1 2.5 1 1.7 1.7 1 2.5 1Z"/></svg>
        </li>
        <li>555.210.4419
          <svg viewBox="0 0 12 12" aria-label="fax"><rect x="3" y="1" width="6" height="3"/><rect x="1" y="4.5" width="10" height="5" rx="1"/><rect x="3" y="8" width="6" height="3" fill="#fff" stroke="#1560ab"/></svg>
        </li>
        <li>555-318.2207
          <svg viewBox="0 0 12 12" aria-label="mobile"><rect x="3" y="0.5" width="6" height="11" rx="1"/><rect x="4" y="2" width="4" height="7" fill="#fff"/></svg>
        </li>
        <li class="web">www.limbwellinc.com
          <svg viewBox="0 0 12 12" aria-label="web"><circle cx="6" cy="6" r="5"/></svg>
        </li>
      </ul>
    </div>
  </section>
</body>
</html>
```